Business Card Design

We need a design for business cards for our company. We have a logo. We teach EMT's and we are based out of Virginia. The information that will need to add would be, name, title, phone number, email, address. On the back of the business card would be "We help you, help others"

Target Market(s)

People that want to become EMT's

Colors

Designer to choose colors to be used in the design.

Requirements
Must have
• company logo

```html
<!DOCTYPE html>
<html lang="en">
<head>
<meta charset="utf-8">
<title>Ridgecare Academy – Business Card</title>
<link href="https://fonts.googleapis.com/css2?family=Montserrat:wght@300;400;600;700&family=Lato:wght@400;700&display=swap" rel="stylesheet">
<style>
  :root {
    --stage: #1b1b1d;
    --card: #1e2436;
    --card-deep: #161b2a;
    --accent: #e8223f;
    --ink: #ffffff;
    --ink-soft: #c9ced9;
    --texture: #2c3447;
  }
  * { box-sizing: border-box; margin: 0; padding: 0; }
  html, body { width: 1200px; height: 900px; overflow: hidden; background: var(--stage); }
  .stage {
    position: relative; width: 1200px; height: 900px;
    display: flex; flex-direction: column; align-items: center; justify-content: center; gap: 24px;
  }
  .card {
    position: relative; width: 700px; height: 400px; overflow: hidden;
    background: linear-gradient(135deg, var(--card) 0%, var(--card-deep) 100%);
    box-shadow: 0 10px 30px rgba(0,0,0,.5);
  }
  .card__texture {
    position: absolute; right: 0; top: 0; width: 300px; height: 100%;
    background: radial-gradient(ellipse at 80% 30%, var(--texture) 0%, rgba(44,52,71,0) 70%);
    opacity: .7;
  }
  .brand {
    position: absolute; display: flex; align-items: center; gap: 14px;
    font-family: "Montserrat", sans-serif; font-weight: 600; color: var(--accent);
    letter-spacing: .02em;
  }
  .brand__dot { width: 16px; height: 16px; border-radius: 50%; background: var(--accent); flex: none; }
  .card--front .brand { left: 140px; top: 150px; font-size: 46px; }
  .tagline {
    position: absolute; left: 330px; top: 250px;
    font-family: "Montserrat", sans-serif; font-weight: 400; font-size: 15px;
    letter-spacing: .04em; color: var(--ink-soft); text-transform: uppercase;
  }
  .card--back .brand { left: 250px; top: 70px; font-size: 34px; }
  .contact {
    position: absolute; left: 70px; bottom: 60px;
    font-family: "Lato", sans-serif; color: var(--ink);
  }
  .contact__name {
    font-family: "Montserrat", sans-serif; font-size: 20px; color: var(--accent);
    text-transform: uppercase; letter-spacing: .02em;
  }
  .contact__first { font-weight: 700; }
  .contact__last { font-weight: 300; }
  .contact__role { font-size: 14px; font-weight: 700; margin: 2px 0 16px; }
  .contact__line { display: flex; align-items: center; gap: 10px; font-size: 15px; margin-top: 5px; }
  .contact__icon { width: 14px; height: 14px; flex: none; }
</style>
</head>
<body>
<main class="stage">
  <section class="card card--front" aria-label="Card front">
    <div class="card__texture" role="img" aria-label="Faint geometric background pattern"></div>
    <div class="brand"><span class="brand__dot"></span>Ridgecare Academy</div>
    <p class="tagline">We help you, help others</p>
  </section>

  <section class="card card--back" aria-label="Card back">
    <div class="card__texture" role="img" aria-label="Faint geometric background pattern"></div>
    <div class="brand"><span class="brand__dot"></span>Ridgecare Academy</div>
    <div class="contact">
      <p class="contact__name"><span class="contact__first">Dana</span> <span class="contact__last">Keller</span></p>
      <p class="contact__role">Founder / Director</p>
      <p class="contact__line">
        <svg class="contact__icon" viewBox="0 0 24 24" aria-hidden="true"><path fill="#e8223f" d="M6.6 10.8a15 15 0 0 0 6.6 6.6l2.2-2.2a1 1 0 0 1 1-.25 11.4 11.4 0 0 0 3.6.57 1 1 0 0 1 1 1V20a1 1 0 0 1-1 1A17 17 0 0 1 3 4a1 1 0 0 1 1-1h3.5a1 1 0 0 1 1 1c0 1.25.2 2.45.57 3.57a1 1 0 0 1-.25 1z"/></svg>
        +1 555 014 2278
      </p>
      <p class="contact__line">
        <svg class="contact__icon" viewBox="0 0 24 24" aria-hidden="true"><rect x="2" y="5" width="20" height="14" rx="1" fill="#e8223f"/><path d="M3 6l9 7 9-7" fill="none" stroke="#1e2436" stroke-width="1.6"/></svg>
        info@ridgecareacademy.com
      </p>
    </div>
  </section>
</main>
</body>
</html>
```